Harborview Estates Business Card for Apartment Buildings

Create business cards for resident managers who run apartment buildings. The audience is the public who are searching for apartment rentals, and current residents who live at the apartment building. Key design element will be incorporating the company logo, however, the logo cannot dominate. The building name and manager name are more important than the logo. Current business card design leaves little room for copy, so we may need to reduce the size on the current card to allow for more space for copy.

Target Market(s)

Adults 18-65 years of age, who are looking for an apartment rental, plus current residents who live at our apartment buildings.

Industry/Entity Type

Property Management

Contact Information for Business Card

A major design element will be use of the company logo. Important property and manager contact information must be part of the design. The size of the logo will need to be reduced to make room for building and manager contact copy.

Font styles to use
Sans Serif

Colors
3176b5
000000
959595
ffffff

Requirements
Must have
• 1) Incorporate the company logo.
• 2) Use the company colors (dark blue, black/grey, over white).
• 3) FEATURE THE BUILDING NAME
• 4) FEATURE THE MANAGER NAME
• 5) The company name is less important than BUILDING and MANAGER
• 6) Manager contact information
• **SEE ATTACHED CREATIVE BRIEF**
Nice to have
• 1) Back of card logo watermark
• 2) Ability to write notes on back of carfd
Should not have
• Avoid letting the company logo dominate the card, the building name and manager are more important than the company logo.

```html
<!DOCTYPE html>
<html lang="en">
<head>
<meta charset="UTF-8">
<title>Harborview Estates – Resident Manager Card</title>
<link rel="stylesheet" href="https://fonts.googleapis.com/css2?family=Open+Sans:ital,wght@0,400;0,600;0,700;1,700&display=swap">
<style>
  :root {
    --brand-blue: #3176b5;
    --deep-blue: #1d62a3;
    --ink: #1f1f1f;
    --grey: #959595;
    --charcoal: #3a3a3a;
    --white: #ffffff;
    --backdrop: #e9ebee;
  }
  * { box-sizing: border-box; margin: 0; padding: 0; }
  html, body { width: 1200px; height: 900px; overflow: hidden; }
  body {
    background: var(--backdrop);
    font-family: "Open Sans", Arial, sans-serif;
    position: relative;
  }
  .card {
    position: absolute;
    left: 250px;
    width: 700px;
    height: 400px;
    border-radius: 22px;
    overflow: hidden;
    box-shadow: 0 10px 28px rgba(0,0,0,0.18);
  }
  .card--front { top: 30px; background: linear-gradient(135deg, #ffffff 0%, #f1f2f3 100%); }
  .card--back  { top: 470px; background: linear-gradient(135deg, var(--brand-blue) 0%, var(--deep-blue) 100%); }

  .front-band { position: absolute; inset: 0; }

  .company-mark {
    position: absolute;
    left: 48px; top: 128px;
    display: flex; align-items: center; gap: 14px;
  }
  .company-mark__square { width: 46px; height: 46px; background: var(--brand-blue); }
  .company-mark__name {
    color: var(--brand-blue);
    font-weight: 700;
    font-size: 26px;
    line-height: 1.05;
    letter-spacing: 0.5px;
    text-transform: uppercase;
  }

  .divider {
    position: absolute;
    left: 352px; top: 105px;
    width: 2px; height: 205px;
    background: var(--brand-blue);
  }

  .manager {
    position: absolute;
    left: 376px; top: 92px;
    color: var(--ink);
    font-size: 15px;
    line-height: 1.42;
  }
  .manager__name {
    color: var(--brand-blue);
    font-weight: 700;
    font-style: italic;
    font-size: 27px;
    line-height: 1.1;
  }
  .manager__title { font-weight: 600; margin-bottom: 2px; }
  .manager__building { font-weight: 600; }
  .contact { list-style: none; margin-top: 4px; }
  .contact li { display: flex; align-items: center; gap: 9px; }
  .contact svg { width: 12px; height: 12px; fill: var(--brand-blue); flex: none; }
  .contact__web { color: var(--brand-blue); }

  .back-content {
    position: absolute; inset: 0;
    display: flex; flex-direction: column; align-items: center; justify-content: center;
    gap: 22px;
    color: var(--white);
  }
  .back-glow {
    position: absolute;
    left: -120px; top: -160px;
    width: 520px; height: 520px; border-radius: 50%;
    background: rgba(255,255,255,0.06);
  }
  .back-mark { display: flex; align-items: center; gap: 18px; position: relative; }
  .back-mark__square { width: 60px; height: 60px; background: var(--white); }
  .back-mark__name {
    font-weight: 700; font-size: 38px; line-height: 1.05;
    text-transform: uppercase; letter-spacing: 1px; color: var(--white);
  }
  .back-web { font-size: 18px; letter-spacing: 1px; position: relative; }
</style>
</head>
<body>

  <section class="card card--front" aria-label="Business card front">
    <svg class="front-band" viewBox="0 0 700 400" preserveAspectRatio="none" aria-hidden="true">
      <path d="M0,300 L410,368" stroke="var(--charcoal)" stroke-width="4" fill="none"/>
      <path d="M0,312 L400,372 Q430,376 450,388 L700,392 L700,400 L0,400 Z" fill="var(--brand-blue)"/>
    </svg>

    <div class="company-mark">
      <span class="company-mark__square"></span>
      <span class="company-mark__name">Harborview<br>Estates LLC</span>
    </div>

    <div class="divider"></div>

    <div class="manager">
      <p class="manager__name">Marisol Ortega</p>
      <p class="manager__title">Resident Manager</p>
      <p class="manager__building">Cedar Crest Apartments</p>
      <p>1452 Linden Avenue</p>
      <p>Lakemont, CA 92150</p>
      <ul class="contact">
        <li><svg viewBox="0 0 24 24"><path d="M6.6 10.8a15 15 0 0 0 6.6 6.6l2.2-2.2a1 1 0 0 1 1-.25 11.4 11.4 0 0 0 3.6.6 1 1 0 0 1 1 1V20a1 1 0 0 1-1 1A17 17 0 0 1 3 4a1 1 0 0 1 1-1h3.5a1 1 0 0 1 1 1c0 1.25.2 2.45.6 3.6a1 1 0 0 1-.25 1z"/></svg>555-210-4471</li>
        <li><svg viewBox="0 0 24 24"><path d="M7 1h10a2 2 0 0 1 2 2v18a2 2 0 0 1-2 2H7a2 2 0 0 1-2-2V3a2 2 0 0 1 2-2zm0 3v14h10V4z"/></svg>555-384-0926</li>
        <li><svg viewBox="0 0 24 24"><path d="M5 8h14a2 2 0 0 1 2 2v6h-3v5H6v-5H3v-6a2 2 0 0 1 2-2zm2-6h10v4H7zm1 12v5h8v-5z"/></svg>555-607-3318</li>
        <li><svg viewBox="0 0 24 24"><path d="M2 5h20v14H2zm2 2v.5l8 5 8-5V7zm0 2.8V17h16V9.8l-8 5z"/></svg>marisol@harborviewest.com</li>
        <li class="contact__web"><svg viewBox="0 0 24 24"><path d="M12 2a10 10 0 1 0 0 20 10 10 0 0 0 0-20zm0 2c.9 0 2.2 2 2.7 5H9.3C9.8 6 11.1 4 12 4zM4.3 11h3a17 17 0 0 0 0 2h-3a8 8 0 0 1 0-2zm5 0h5.4a15 15 0 0 1 0 2H9.3a15 15 0 0 1 0-2zm7.4 0h3a8 8 0 0 1 0 2h-3a17 17 0 0 0 0-2zM9.3 15h5.4c-.5 3-1.8 5-2.7 5s-2.2-2-2.7-5z"/></svg>www.harborviewest.com</li>
      </ul>
    </div>
  </section>

  <section class="card card--back" aria-label="Business card back">
    <div class="back-glow"></div>
    <div class="back-content">
      <div class="back-mark">
        <span class="back-mark__square"></span>
        <span class="back-mark__name">Harborview<br>Estates LLC</span>
      </div>
      <p class="back-web">www.harborviewest.com</p>
    </div>
  </section>

</body>
</html>
```